Brackwell Yard Services Flyer Design

I need a new flyer design for my business, Brackwell Yard Services. I’ll be providing my old flyer and logo as references. The new flyer should feature updated wording, contact information, logos, and photos, but still keep the original “What We Do” section and include the phrase “Don’t See? Just Ask!” somewhere near the services. The flyer needs to look great in black and white for door-to-door handouts but also be eye-catching and professional enough for social media use.

The updated content should include the headline “Transforming Outdoor Spaces with Hard Work & Precision” and highlight three main service areas: Landscaping Services (project-based landscaping to clean, prepare, and transform outdoor spaces with precision), Property Cleanup (quick hauls, debris removal, or full cleanouts—no job too big or small), and Ground Preparation (pad preparation, brush removal, and fire lines—making properties safe, functional, and project-ready).

Please also include a “Why Choose Us?” section that lists: Locally owned since 2022, Reliable & affordable – no corners cut, Professional results you can trust, LICENSED AND Insured, and Quality work / on time / references / flexible / follow-up.

At the bottom, include the contact details: Call or Text Today!
www.brackwellyard.example
| sales@brackwellyard.example
| (555) 014-7293

The overall design should be clean, professional, and easy to read with a layout that clearly shows what we offer. Use visuals that represent outdoor services, landscaping, and property cleanup/prep work. I want something that feels trustworthy, family-friendly, and modern.
Use the same photo of leaf clean up from the original flyer if possible.
Our company colors are also black and white. For the most part.

```html
<!DOCTYPE html>
<html lang="en">
<head>
<meta charset="utf-8">
<title>Brackwell Yard Services Flyer</title>
<link href="https://fonts.googleapis.com/css2?family=Roboto:wght@400;500;700;900&display=swap" rel="stylesheet">
<style>
:root{
  --orange:#e8642a;
  --ink:#231f20;
  --dark:#2a2627;
  --paper:#ffffff;
  --mist:#e9e9e9;
  --stage:#6b6b6b;
}
*{margin:0;padding:0;box-sizing:border-box}
html,body{width:1200px;height:681px;overflow:hidden;background:var(--stage)}
body{font-family:'Roboto',Arial,sans-serif;position:relative}
.flyer{position:absolute;left:366px;top:10px;width:920px;height:1300px;transform:scale(0.5077);transform-origin:0 0;background:var(--paper);overflow:hidden;box-shadow:0 10px 30px rgba(0,0,0,.35)}
.abs{position:absolute}
.hero-photo{left:380px;top:0;width:540px;height:356px;background:linear-gradient(90deg,rgba(255,255,255,1) 0%,rgba(215,215,215,.7) 35%,#cfcfcf 100%)}
.brand{left:55px;top:72px;display:flex;align-items:center;gap:14px;font-weight:900;font-size:36px;color:var(--ink);letter-spacing:.5px}
.brand-mark{width:40px;height:40px;background:var(--ink)}
.headline{left:55px;top:170px;color:var(--ink);line-height:1}
.headline .l1{font-size:46px;font-weight:500}
.headline .l2{font-size:74px;font-weight:900;color:var(--orange);margin-top:6px;letter-spacing:1px}
.headline .l3{font-size:45px;font-weight:500;margin-top:4px}
.band-dark{left:0;top:356px;width:920px;height:204px;background:var(--dark)}
.band-mist{left:0;top:560px;width:920px;height:240px;background:linear-gradient(180deg,#e4e4e4,#fff)}
.service-photo{top:372px;width:235px;height:262px;border-radius:18px;border:5px solid #d8d8d8}
.ph1{left:82px;background:linear-gradient(160deg,#6f7a3a,#a8873f 55%,#6a3a1c)}
.ph2{left:342px;background:linear-gradient(160deg,#7d8a9a,#5c5046 50%,#3a3a36)}
.ph3{left:602px;background:linear-gradient(170deg,#9fb6cf,#8d8f86 45%,#a7a39a)}
.divider{top:605px;width:2px;height:150px;background:var(--ink)}
.service{top:650px;width:250px;text-align:center}
.service h3{color:var(--orange);font-size:22px;font-weight:700;line-height:1}
.service p{color:var(--ink);font-size:15.5px;line-height:18px;margin-top:12px}
.offer-box{left:57px;top:802px;width:806px;height:215px;border:3px solid var(--orange);border-radius:16px}
.col{top:842px}
.col h4{color:var(--orange);font-size:21px;font-weight:700;letter-spacing:.3px}
.col ul{list-style:none;margin-top:12px}
.col li{font-size:17px;color:var(--ink);height:26px;display:flex;align-items:center;gap:12px}
.col li svg{flex:none}
.why-list{top:1090px;list-style:none;color:#fff;font-size:17px;line-height:22px}
.why-list li::before{content:"";display:inline-block;width:5px;height:5px;background:#fff;margin-right:11px;vertical-align:middle}
.contacts{left:0;top:1232px;width:920px;display:flex;justify-content:center;gap:38px;align-items:center;color:#fff;font-size:17px}
.contacts span{display:flex;align-items:center;gap:10px}
.contacts .phone{font-size:22px;font-weight:700}
.why-title{left:78px;top:1142px;font-size:21px;font-weight:700;color:#fff}
.why-title b{color:var(--orange)}
</style>
</head>
<body>
<main class="flyer">
  <div class="abs hero-photo" role="img" aria-label="Faded landscaped home garden with trees and shrubs"></div>
  <div class="abs brand"><span class="brand-mark"></span>Brackwell Yard Services</div>
  <div class="abs headline">
    <div class="l1">TRANSFORMING</div>
    <div class="l2">OUTDOOR SPACES</div>
    <div class="l3">WITH HARD WORK &amp; PRECISION</div>
  </div>

  <div class="abs band-dark"></div>
  <div class="abs band-mist"></div>

  <div class="abs service-photo ph1" role="img" aria-label="Rake and bag of collected autumn leaves on a lawn"></div>
  <div class="abs service-photo ph2" role="img" aria-label="Truck bed loaded with junk and debris"></div>
  <div class="abs service-photo ph3" role="img" aria-label="Prepared gravel pad beside a house and wooden fence"></div>

  <div class="abs divider" style="left:331px"></div>
  <div class="abs divider" style="left:591px"></div>

  <div class="abs service" style="left:75px"><h3>LANDSCAPING<br>SERVICES</h3><p>Project-based landscaping to clean, prepare, and transform outdoor spaces with precision</p></div>
  <div class="abs service" style="left:335px"><h3>PROPERTY<br>CLEANUP</h3><p>Quick hauls, debris removal, or full cleanouts—no job too big or small</p></div>
  <div class="abs service" style="left:595px;width:250px"><h3>GROUND<br>PREPARATION</h3><p>Pad preparation, brush removal, and fire lines—making properties safe, functional, and project-ready</p></div>

  <div class="abs offer-box"></div>
  <svg class="abs" style="left:335px;top:781px" width="250" height="42" viewBox="0 0 250 42"><path d="M10 0H240L232 42H2Z" fill="var(--orange)"/><text x="121" y="29" text-anchor="middle" fill="#fff" font-family="Roboto,sans-serif" font-size="21" font-weight="500">WHAT WE DO</text></svg>

  <div class="abs col" style="left:112px"><h4>REMOVE</h4><ul>
    <li><svg width="17" height="17" viewBox="0 0 17 17"><rect width="17" height="17" rx="2" fill="var(--orange)"/><path d="M4 9l3 3 6-7" stroke="#fff" stroke-width="2.2" fill="none"/></svg>Junk Removal</li>
    <li><svg width="17" height="17" viewBox="0 0 17 17"><rect width="17" height="17" rx="2" fill="var(--orange)"/><path d="M4 9l3 3 6-7" stroke="#fff" stroke-width="2.2" fill="none"/></svg>Trash &amp; Waste Hauling</li>
    <li><svg width="17" height="17" viewBox="0 0 17 17"><rect width="17" height="17" rx="2" fill="var(--orange)"/><path d="M4 9l3 3 6-7" stroke="#fff" stroke-width="2.2" fill="none"/></svg>Yard &amp; Garden Cleanup</li>
    <li><svg width="17" height="17" viewBox="0 0 17 17"><rect width="17" height="17" rx="2" fill="var(--orange)"/><path d="M4 9l3 3 6-7" stroke="#fff" stroke-width="2.2" fill="none"/></svg>Appliance Removal</li>
  </ul></div>
  <div class="abs col" style="left:389px"><h4>INSTALL</h4><ul>
    <li><svg width="17" height="17" viewBox="0 0 17 17"><rect width="17" height="17" rx="2" fill="var(--orange)"/><path d="M4 9l3 3 6-7" stroke="#fff" stroke-width="2.2" fill="none"/></svg>Mulch</li>
    <li><svg width="17" height="17" viewBox="0 0 17 17"><rect width="17" height="17" rx="2" fill="var(--orange)"/><path d="M4 9l3 3 6-7" stroke="#fff" stroke-width="2.2" fill="none"/></svg>D.C.</li>
    <li><svg width="17" height="17" viewBox="0 0 17 17"><rect width="17" height="17" rx="2" fill="var(--orange)"/><path d="M4 9l3 3 6-7" stroke="#fff" stroke-width="2.2" fill="none"/></svg>Plants</li>
    <li><svg width="17" height="17" viewBox="0 0 17 17"><rect width="17" height="17" rx="2" fill="var(--orange)"/><path d="M4 9l3 3 6-7" stroke="#fff" stroke-width="2.2" fill="none"/></svg>Rock</li>
  </ul></div>
  <div class="abs col" style="left:520px"><h4>MAINTENANCE &amp; OTHER</h4><ul>
    <li><svg width="17" height="17" viewBox="0 0 17 17"><rect width="17" height="17" rx="2" fill="var(--orange)"/><path d="M4 9l3 3 6-7" stroke="#fff" stroke-width="2.2" fill="none"/></svg>Yard Cleanup</li>
    <li><svg width="17" height="17" viewBox="0 0 17 17"><rect width="17" height="17" rx="2" fill="var(--orange)"/><path d="M4 9l3 3 6-7" stroke="#fff" stroke-width="2.2" fill="none"/></svg>Weed Prevention (Pre-emergent)</li>
    <li><svg width="17" height="17" viewBox="0 0 17 17"><rect width="17" height="17" rx="2" fill="var(--orange)"/><path d="M4 9l3 3 6-7" stroke="#fff" stroke-width="2.2" fill="none"/></svg>Roof &amp; Gutter Cleaning</li>
    <li><svg width="17" height="17" viewBox="0 0 17 17"><rect width="17" height="17" rx="2" fill="var(--orange)"/><path d="M4 9l3 3 6-7" stroke="#fff" stroke-width="2.2" fill="none"/></svg>Fence &amp; Deck Staining</li>
  </ul></div>

  <svg class="abs" style="left:522px;top:992px" width="290" height="40" viewBox="0 0 290 40"><path d="M0 20H10M280 20H290" stroke="var(--orange)" stroke-width="3"/><path d="M14 0H284L276 40H6Z" fill="var(--dark)"/><text x="145" y="28" text-anchor="middle" fill="var(--orange)" font-family="Roboto,sans-serif" font-size="21" font-weight="700">DON’T SEE IT, JUST ASK</text></svg>

  <svg class="abs" style="left:0;top:1040px" width="920" height="260" viewBox="0 0 920 260">
    <path d="M420 80 Q440 5 520 5 H920 V80Z" fill="var(--dark)"/>
    <rect x="0" y="42" width="920" height="125" fill="var(--orange)"/>
    <rect x="0" y="167" width="920" height="93" fill="var(--dark)"/>
    <path d="M0 -2 H322 Q332 -2 328 10 L296 132 Q292 146 278 146 H0Z" fill="#fff"/>
  </svg>
  <div class="abs" style="left:0;top:1044px;width:316px;height:136px;background:linear-gradient(120deg,#6e7f3c,#8a9b5a 40%,#3f7fc4 75%,#2d5f9e);clip-path:polygon(0 0,100% 0,87% 100%,0 100%);border-radius:0 12px 12px 0" role="img" aria-label="Blue trash bags and a rake on a cleared lawn"></div>
  <div class="abs why-title"><b>Why</b> Choose Us?</div>

  <ul class="abs why-list" style="left:365px">
    <li>Locally owned since 2022</li>
    <li>Reliable &amp; affordable – no corners cut</li>
    <li>Professional results you can trust</li>
    <li>LICENSED AND Insured</li>
    <li>Quality work</li>
  </ul>
  <ul class="abs why-list" style="left:715px">
    <li>On time</li>
    <li>References</li>
    <li>Flexible</li>
    <li>Follow-up.</li>
  </ul>

  <div class="abs contacts">
    <span class="phone"><svg width="20" height="20" viewBox="0 0 24 24"><path d="M6.6 10.8a15 15 0 006.6 6.6l2.2-2.2a1 1 0 011-.25 11 11 0 003.5.56 1 1 0 011 1V20a1 1 0 01-1 1A17 17 0 013 4a1 1 0 011-1h3.5a1 1 0 011 1 11 11 0 00.56 3.5 1 1 0 01-.25 1z" fill="var(--orange)"/></svg>(555) 014-7293</span>
    <span><svg width="20" height="20" viewBox="0 0 24 24" fill="none" stroke="var(--orange)" stroke-width="2"><circle cx="12" cy="12" r="9"/><path d="M3 12h18M12 3c3 3 3 15 0 18M12 3c-3 3-3 15 0 18"/></svg>www.brackwellyard.example</span>
    <span><svg width="22" height="16" viewBox="0 0 22 16"><rect width="22" height="16" rx="1" fill="var(--orange)"/><path d="M1 1l10 8 10-8" stroke="var(--dark)" stroke-width="1.6" fill="none"/></svg>sales@brackwellyard.example</span>
  </div>
</main>
</body>
</html>
```